Maple9Tone

I need a website designed to feature a new product for my company. I am dedicating a separate site just highlight the program. The url will be maple9tone.com and the product name is maple tone. The product is ringless voicemail. We take a recorded script and send it to our clients customers cell phones without the phone ringing.

The site will consist of a home page. I animated video demo. It will house 18 scripts and voice overs to match, a results page, and a page to request a live demo.

We sell the product to new car dealerships

```html
<!DOCTYPE html>
<html lang="en">
<head>
<meta charset="utf-8">
<title>Maple9Tone – Ringless Voicemail</title>
<link rel="stylesheet" href="https://fonts.googleapis.com/css2?family=Open+Sans:wght@400;600;700;800&family=Lato:wght@400;700;900&display=swap">
<style>
:root{
  --accent-red:#e8413c;
  --ink:#2b2b2b;
  --muted:#7a7a7a;
  --blue:#2f9fdc;
  --blue-deep:#1f87c8;
  --pink:#f2586b;
  --slate:#5d7a93;
  --footer:#1e1e20;
  --footer-base:#141416;
  --white:#ffffff;
  --line:#e6e6e6;
}
*{box-sizing:border-box;margin:0;padding:0}
html,body{width:1200px;height:2988px;overflow:hidden}
body{position:relative;font-family:"Open Sans",Arial,sans-serif;color:var(--ink);background:var(--white)}
.abs{position:absolute}

/* header */
.site-header{left:0;top:0;width:1200px;height:60px;background:var(--white);border-bottom:1px solid var(--line)}
.brand{left:40px;top:15px;font-family:"Open Sans",sans-serif;font-weight:700;font-size:22px;line-height:30px;color:var(--ink)}
.main-nav{right:40px;top:0;height:60px;display:flex;gap:0}
.main-nav a{display:block;padding:0 18px;line-height:56px;font-size:13px;font-weight:600;color:#555;text-decoration:none;letter-spacing:.5px;border-top:3px solid transparent}
.main-nav a.active{color:var(--accent-red);border-top-color:var(--accent-red)}

/* hero */
.hero{left:0;top:60px;width:1200px;height:508px;background:linear-gradient(110deg,#2d3136 0%,#4a4f55 45%,#8a8f93 70%,#3c4045 100%)}
.hero-title{left:100px;top:225px;font-family:"Lato",sans-serif;font-weight:700;font-size:46px;line-height:52px;color:var(--white)}
.hero-dots{left:100px;top:396px;display:flex;gap:10px}
.hero-dots span{width:14px;height:14px;border-radius:50%;border:2px solid var(--white)}
.hero-dots span.on{background:var(--blue)}

/* welcome */
.welcome-title{left:0;top:620px;width:1200px;text-align:center;font-family:"Lato",sans-serif;font-weight:900;font-size:34px;letter-spacing:1px;color:var(--ink)}
.welcome-rule{left:570px;top:672px;width:60px;height:3px;background:var(--accent-red)}
.welcome-copy{left:120px;top:695px;width:960px;text-align:center;font-size:12px;line-height:20px;color:var(--muted)}
.welcome-art{left:380px;top:780px;width:200px;height:170px;background:radial-gradient(circle at 50% 45%,#9bd3f1 0%,#e8f4fb 70%,#ffffff 100%)}
.benefit-list{left:640px;top:790px;list-style:none}
.benefit-list li{display:flex;align-items:center;gap:18px;height:40px;font-family:"Lato",sans-serif;font-weight:700;font-size:16px;letter-spacing:1px;color:#333}

/* how it works */
.how{left:0;top:960px;width:1200px;height:760px;background:var(--blue);clip-path:polygon(0 44px,50% 0,100% 44px,100% 100%,0 100%)}
.how-title{left:0;top:1060px;width:1200px;text-align:center;font-family:"Lato",sans-serif;font-weight:900;font-size:34px;letter-spacing:1px;color:var(--white)}
.how-rule{left:570px;top:1110px;width:60px;height:3px;background:var(--white)}
.step-text{width:300px;font-size:12.5px;line-height:19px;color:var(--white)}
.step-text.left{left:130px;text-align:right}
.step-text.right{left:800px}
.how-arrows{left:0;top:960px}

/* scripts */
.scripts-art{left:160px;top:1800px;width:400px;height:250px;background:linear-gradient(160deg,#d8eef8 0%,#a9d7ef 60%,#7ab8dc 100%)}
.scripts-title{left:600px;top:1796px;font-family:"Lato",sans-serif;font-weight:700;font-size:34px;color:var(--ink)}
.script-list{top:1860px;list-style:none;font-size:11.5px;line-height:21px;color:#555}
.script-list li::before{content:"";display:inline-block;width:7px;height:7px;border-radius:50%;background:var(--blue);margin-right:10px;vertical-align:1px}

/* offer */
.offer-art{left:0;top:2100px;width:600px;height:340px;background:linear-gradient(135deg,#6f8ca4 0%,#536f88 60%,#465f76 100%)}
.offer-panel{left:600px;top:2100px;width:600px;height:340px;background:var(--pink)}
.offer-title{left:620px;top:2160px;font-family:"Lato",sans-serif;font-weight:900;font-size:44px;color:var(--white);letter-spacing:1px}
.offer-sub{left:620px;top:2212px;font-family:"Lato",sans-serif;font-weight:700;font-size:20px;color:var(--white);letter-spacing:2px}
.offer-list{left:620px;top:2250px;list-style:none;font-size:12px;line-height:22px;color:var(--white)}
.offer-list li::before{content:"✓";margin-right:10px;font-weight:700}

/* dealer names */
.dealers{left:0;top:2460px;width:1200px;height:150px;display:flex;justify-content:center;align-items:center;gap:70px;font-family:"Lato",sans-serif;font-weight:700;font-size:22px;color:#3a3a3a}

/* footer */
.site-footer{left:0;top:2620px;width:1200px;height:320px;background:var(--footer);color:#bdbdbd}
.footer-heading{font-family:"Lato",sans-serif;font-weight:700;font-size:16px;letter-spacing:1px;color:var(--white)}
.footer-copy{font-size:11.5px;line-height:19px}
.email-field{left:40px;top:2728px;width:200px;height:34px;border:1px solid #444;background:#2a2a2d;color:#888;font-size:12px;padding:8px 10px}
.subscribe{left:40px;top:2778px;width:110px;height:34px;background:var(--blue-deep);color:var(--white);font-size:12px;font-weight:700;text-align:center;line-height:34px;letter-spacing:1px}
.contact-row{display:flex;align-items:flex-start;gap:10px;font-size:11.5px;line-height:18px;margin-bottom:10px}
.results-list{list-style:none;font-size:11.5px;line-height:21px}
.results-list li::before{content:"•";color:var(--white);margin-right:8px}
.footer-base{left:0;top:2940px;width:1200px;height:48px;background:var(--footer-base);color:#888;font-size:11px;text-align:center;line-height:48px}
</style>
</head>
<body>

<header class="site-header abs">
  <div class="brand abs">Maple9Tone</div>
  <nav class="main-nav abs">
    <a class="active" href="#">HOME</a><a href="#">ABOUT US</a><a href="#">PRODUCT</a><a href="#">BLOG</a><a href="#">CONTACT US</a>
  </nav>
</header>

<section class="hero abs" role="img" aria-label="Photo of a hand holding a smartphone showing an incoming voicemail envelope"></section>
<h1 class="hero-title abs">Fast, Effective,<br>Inexpensive,<br>Versatile Marketing.</h1>
<div class="hero-dots abs"><span class="on"></span><span></span><span></span></div>

<h2 class="welcome-title abs">WELCOME TO MAPLE 9 TONE</h2>
<div class="welcome-rule abs"></div>
<p class="welcome-copy abs">Maple tone delivers your recorded message straight to the voicemail box of your customers without ever ringing their phone. Dealerships use it to announce sales events, service specials and trade-in offers, reaching hundreds of prospects in minutes. Your message arrives personal, on time and heard in full, so more buyers call back and more service lanes fill up every week.</p>
<div class="welcome-art abs" role="img" aria-label="Illustration of a hand holding a phone with a microphone on screen"></div>
<ul class="benefit-list abs">
  <li><svg width="26" height="26" viewBox="0 0 26 26"><circle cx="13" cy="13" r="12" fill="none" stroke="#333" stroke-width="1.6"/><path d="M7 13.5l4 4 8-9" fill="none" stroke="#333" stroke-width="2"/></svg>FAST</li>
  <li><svg width="26" height="26" viewBox="0 0 26 26"><circle cx="13" cy="13" r="12" fill="none" stroke="#333" stroke-width="1.6"/><path d="M7 13.5l4 4 8-9" fill="none" stroke="#333" stroke-width="2"/></svg>EFFECTIVE</li>
  <li><svg width="26" height="26" viewBox="0 0 26 26"><circle cx="13" cy="13" r="12" fill="none" stroke="#333" stroke-width="1.6"/><path d="M7 13.5l4 4 8-9" fill="none" stroke="#333" stroke-width="2"/></svg>INEXPENSIVE</li>
  <li><svg width="26" height="26" viewBox="0 0 26 26"><circle cx="13" cy="13" r="12" fill="none" stroke="#333" stroke-width="1.6"/><path d="M7 13.5l4 4 8-9" fill="none" stroke="#333" stroke-width="2"/></svg>VERSATILE MARKETING</li>
</ul>

<section class="how abs"></section>
<h2 class="how-title abs">HOW IT WORKS</h2>
<div class="how-rule abs"></div>

<svg class="how-arrows abs" width="1200" height="760" viewBox="0 0 1200 760" aria-hidden="true">
  <g fill="none" stroke="#fff" stroke-width="2.5">
    <path d="M530 235 C610 235 640 215 700 190"/>
    <path d="M530 355 C620 345 650 300 700 220"/>
    <path d="M530 470 C620 470 650 420 700 250"/>
    <path d="M530 595 C600 590 640 560 700 490"/>
  </g>
  <g fill="#fff">
    <path d="M700 182l8 4-6 8z"/><path d="M703 212l2 12-9-5z"/><path d="M703 242l2 12-9-5z"/><path d="M702 482l1 12-9-4z"/>
  </g>
  <g fill="#fff">
    <circle cx="510" cy="235" r="30"/><circle cx="510" cy="355" r="30"/><circle cx="510" cy="470" r="30"/><circle cx="510" cy="595" r="30"/>
    <circle cx="740" cy="200" r="30"/><circle cx="740" cy="320" r="30"/><circle cx="740" cy="440" r="30"/><circle cx="740" cy="570" r="30"/>
  </g>
  <g fill="none" stroke="#2f9fdc" stroke-width="2.5">
    <circle cx="510" cy="228" r="6"/><path d="M498 248c2-8 22-8 24 0"/>
    <rect x="497" y="344" width="26" height="22" rx="2"/><path d="M497 351h26M504 340v6M516 340v6"/>
    <rect x="504" y="456" width="12" height="18" rx="6"/><path d="M499 468c0 9 22 9 22 0M510 477v6"/>
    <rect x="496" y="584" width="28" height="18" rx="2"/><path d="M504 608h12"/>
    <path d="M728 196a13 13 0 0 1 24 0M752 204a13 13 0 0 1-24 0"/><path d="M752 190v7h-7M728 210v-7h7"/>
    <path d="M730 312h20v18h-20zM735 320l5 4 6-8"/>
    <circle cx="740" cy="440" r="13"/><path d="M740 432v9l6 4"/>
    <path d="M727 574v-6a13 13 0 0 1 26 0v6"/><rect x="724" y="572" width="6" height="10" rx="2"/><rect x="750" y="572" width="6" height="10" rx="2"/>
  </g>
</svg>

<p class="step-text left abs" style="top:1178px">We select a targeted list of your sales prospects, service customers or social leads.</p>
<p class="step-text left abs" style="top:1296px">We develop your script based on your current service needs, incentives, time of year and more.</p>
<p class="step-text left abs" style="top:1410px">Your team will be recorded and given a set of scripts so responses to your message stay consistent.</p>
<p class="step-text left abs" style="top:1536px">Your message and list are uploaded to our system and delivered at the best time of day.</p>
<p class="step-text right abs" style="top:1148px">Inbound phone calls will begin within minutes of your message landing.</p>
<p class="step-text right abs" style="top:1268px">This program captures more leads for your sales and service teams.</p>
<p class="step-text right abs" style="top:1390px">The whole process above can be completed and go live in as little as 24 hours.</p>
<p class="step-text right abs" style="top:1520px">Every inbound phone call is recorded, tracked and called-back reporting is updated.</p>

<div class="scripts-art abs" role="img" aria-label="Illustration of two people with a video player and speech bubble between them"></div>
<h2 class="scripts-title abs">Available Scripts</h2>
<ul class="script-list abs" style="left:600px">
  <li>January Start Sale</li><li>February Winter Special</li><li>March Spring Event</li><li>Spring Tax Refund</li><li>April Trip Time</li><li>May Memorial Day</li><li>June Summer Savings</li><li>July Independence Day</li><li>August Model Year-End</li><li>September Labor Day</li>
</ul>
<ul class="script-list abs" style="left:860px">
  <li>October Fall Service Savings</li><li>November Giving Thanks Event</li><li>December Happy Holiday Sale</li>
</ul>

<div class="offer-art abs" role="img" aria-label="Illustration of a phone sending envelopes across a web-address patterned backdrop"></div>
<section class="offer-panel abs"></section>
<h2 class="offer-title abs">OFFER</h2>
<p class="offer-sub abs">MAPLE 9 TONE</p>
<ul class="offer-list abs">
  <li>We can run this on a trial basis to prove results</li>
  <li>Messages delivered to your full customer list</li>
  <li>To be recorded by a professional voice</li>
  <li>Scripts written to match the current season</li>
  <li>The information stays with you</li>
</ul>

<div class="dealers abs">
  <span>Northline</span><span>Beacon</span><span>Garrison</span><span>Ridgeway</span><span>Summit</span><span>Crestline</span>
</div>

<footer class="site-footer abs">
  <div class="abs" style="left:40px;top:30px;width:280px">
    <h3 class="footer-heading">JOIN OUR MAILING LIST</h3>
    <p class="footer-copy" style="margin-top:10px">Receive new scripts and results updates directly in your inbox as soon as they are released.</p>
  </div>
  <div class="abs" style="left:420px;top:30px;width:280px">
    <h3 class="footer-heading">CONTACT US</h3>
    <div style="margin-top:14px">
      <div class="contact-row"><svg width="14" height="16" viewBox="0 0 14 16"><path d="M7 1a5 5 0 0 1 5 5c0 4-5 9-5 9S2 10 2 6a5 5 0 0 1 5-5z" fill="#bdbdbd"/></svg><span>214 Birch Lane<br>Dayton, OH 45402</span></div>
      <div class="contact-row"><svg width="14" height="14" viewBox="0 0 14 14"><path d="M3 1l3 3-2 2c1 2 2 3 4 4l2-2 3 3-2 2C6 13 1 8 1 3z" fill="#bdbdbd"/></svg><span>Phone: (555) 555-0143<br>Fax: (555) 555-0187</span></div>
      <div class="contact-row"><svg width="14" height="12" viewBox="0 0 14 12"><rect x="1" y="1" width="12" height="10" fill="none" stroke="#bdbdbd"/><path d="M1 1l6 5 6-5" fill="none" stroke="#bdbdbd"/></svg><span>hello@maple9tone.com</span></div>
    </div>
  </div>
  <div class="abs" style="left:800px;top:30px;width:360px">
    <h3 class="footer-heading">RESULTS</h3>
    <ul class="results-list" style="margin-top:12px">
      <li>Metro Dealer - 241 inbound calls</li>
      <li>Coastal Dealer - 363 inbound calls</li>
      <li>Valley Dealer - 96 inbound calls</li>
      <li>Lakeside Dealer - 310 inbound calls</li>
      <li>Hillcrest Dealer - 188 inbound calls</li>
      <li>Harbor Dealer - 143 service calls and more</li>
    </ul>
  </div>
</footer>
<div class="email-field abs">Enter email</div>
<div class="subscribe abs">SUBSCRIBE</div>
<div class="footer-base abs">Copyright 2016 | All Rights Reserved | Maple9Tone</div>

</body>
</html>
```